Frostvale Harborline LLC

we need a business card design

Industry/Entity Type

hvac

Contact Information for Business Card

my logo

Requirements
Must have
• my logo and same colors

```html
<!DOCTYPE html>
<html lang="en">
<head>
<meta charset="utf-8">
<title>Frostvale Harborline LLC — Business Card</title>
<link href="https://fonts.googleapis.com/css2?family=Montserrat:wght@400;700&display=swap" rel="stylesheet">
<style>
  :root {
    --page-bg: #d6d6d6;
    --card-bg: #ffffff;
    --brand-blue: #1d57a8;
    --ink: #333333;
    --icon-blue: #1d57a8;
  }
  * { margin: 0; padding: 0; box-sizing: border-box; }
  html, body {
    width: 1200px; height: 896px; overflow: hidden;
    background: var(--page-bg);
    font-family: "Montserrat", sans-serif;
  }
  .card {
    position: absolute;
    left: 334px;
    width: 527px; height: 300px;
    background: var(--card-bg);
    border-radius: 28px;
    box-shadow: 0 14px 24px rgba(0,0,0,0.18);
  }
  .card-front { top: 126px; display: flex; align-items: center; justify-content: center; }
  .card-back  { top: 475px; }

  .brand-name {
    color: var(--brand-blue);
    font-weight: 700;
    text-align: center;
    line-height: 1.15;
    text-transform: uppercase;
  }
  .card-front .brand-name { font-size: 34px; }
  .card-back .brand-name {
    position: absolute; left: 30px; top: 112px; width: 220px;
    font-size: 21px;
  }

  .divider {
    position: absolute; left: 273px; top: 65px;
    width: 1.5px; height: 172px;
    background: var(--brand-blue);
  }
  .details { position: absolute; left: 294px; top: 60px; color: var(--ink); }
  .person-name { font-size: 24px; font-weight: 700; color: var(--brand-blue); letter-spacing: 0.3px; }
  .person-title { font-size: 14px; margin-top: 2px; }
  .address { font-size: 14px; line-height: 21px; margin-top: 16px; }
  .contact-list { list-style: none; margin-top: 12px; font-size: 14px; line-height: 21px; }
  .contact-list li { display: flex; align-items: center; gap: 7px; }
  .contact-list svg { width: 11px; height: 11px; fill: var(--icon-blue); }
</style>
</head>
<body>
  <section class="card card-front">
    <div class="brand-name">Frostvale<br>Harborline LLC</div>
  </section>

  <section class="card card-back">
    <div class="brand-name">Frostvale<br>Harborline LLC</div>
    <div class="divider"></div>
    <div class="details">
      <div class="person-name">DANIEL REYES</div>
      <div class="person-title">Managing Director</div>
      <div class="address">Your address, City<br>State, Zip 1234</div>
      <ul class="contact-list">
        <li><svg viewBox="0 0 12 12"><path d="M1 5 Q6 0 11 5 L9 6 L8 4.5 H4 L3 6 Z M3 7 H9 L10 11 H2 Z"/></svg>123 456 789</li>
        <li><svg viewBox="0 0 12 12"><path d="M0 2 H12 V10 H0 Z M0 2 L6 7 L12 2 V3.4 L6 8.4 L0 3.4 Z" fill-rule="evenodd"/></svg>info@yourmail.com</li>
        <li><svg viewBox="0 0 12 12"><circle cx="6" cy="6" r="5.5"/><path d="M3 3 Q5 5 4 8 M8 2 Q7 5 9 8" stroke="#fff" stroke-width="1" fill="none"/></svg>www.yourwebsite.com</li>
      </ul>
    </div>
  </section>
</body>
</html>
```